Pitch Deck presentation

Design multiple graphics and slides that can be used in a PowerPoint presentation.
4 infographics, text templates and blank templates
Attached you will find the infographics references and a couple of styles we would like to have on the presentations
We prefer a simpler design with not too much background noise or colors(prefer to have whiter backgrounds)
The infographics in the whiteboard should be presented 1 per slide with space on the right side to write text for explanation.
4 total columns will be the equivalent to the 4 different slides with design in the presentation.
Attached you have our colors and logos.
https://files.plomvarek.net/share/7qKtr2WnZe4xBvLp9HsD3aYuM0cFgR?mode=view
You can reach out to me with any questions at my email mkestrubio@hallowpine.com

```html
<!DOCTYPE html>
<html lang="en">
<head>
<meta charset="utf-8">
<title>Haulway Pitch Deck Slides</title>
<link href="https://fonts.googleapis.com/css2?family=Oswald:wght@300;400;600;700&family=Open+Sans:wght@400;600&display=swap" rel="stylesheet">
<style>
  :root{
    --board:#636363;
    --paper:#ffffff;
    --ink:#2b2b2b;
    --ink-soft:#555555;
    --orange:#e8501e;
    --orange-deep:#d9451a;
    --grid:#eeeeee;
    --rule:#dddddd;
  }
  *{margin:0;padding:0;box-sizing:border-box}
  html,body{width:1066px;height:1200px;overflow:hidden;background:var(--board)}
  body{position:relative;font-family:"Oswald",sans-serif;color:var(--ink)}
  .slide{position:absolute;width:458px;height:257px;background:var(--paper);box-shadow:0 3px 8px rgba(0,0,0,.35);overflow:hidden}
  .col-left{left:67.5px}.col-right{left:540px}
  .row-1{top:65px}.row-2{top:336px}.row-3{top:607px}.row-4{top:878px}
  .abs{position:absolute}
  .brand-mini{position:absolute;right:15px;top:11px;font-family:"Oswald",sans-serif;font-weight:600;font-size:15px;letter-spacing:.5px;color:var(--ink);line-height:1}
  .page-no{position:absolute;right:4px;bottom:4px;font-size:3.6px;font-weight:600;color:var(--ink);letter-spacing:.2px}
  .page-no b{color:var(--orange);font-weight:600}
  .heading{position:absolute;font-weight:600;font-size:20px;line-height:1;padding:2px 2px 1px;border-top:1.5px solid var(--orange);border-bottom:1.5px solid var(--ink);color:var(--ink);letter-spacing:.2px;white-space:nowrap}
  .heading .accent{color:var(--orange)}
  .body-copy{position:absolute;font-weight:300;font-size:6.9px;line-height:12.8px;color:var(--ink-soft);text-align:justify}

  /* title slide */
  .title-brand{position:absolute;left:0;right:0;top:16px;text-align:center;font-weight:600;font-size:50px;line-height:1;letter-spacing:2px;color:var(--ink)}
  .band{position:absolute;left:10.5px;width:437.5px;height:17px;background:var(--orange)}
  .hero-photo{position:absolute;left:16px;top:106px;width:426px;height:116px;background:linear-gradient(100deg,#2a2a2e 0%,#4c4c52 45%,#6a6a70 70%,#2d2d31 100%)}
  .hero-title{position:absolute;left:16px;top:106px;width:426px;height:116px;display:flex;align-items:center;justify-content:center;font-weight:400;font-size:48px;color:#fff;letter-spacing:-.5px;text-shadow:2px 2px 0 var(--orange-deep)}

  /* why choose us */
  .option-title{position:absolute;font-family:"Open Sans",sans-serif;font-weight:600;font-size:6px;color:var(--ink)}
  .option-text{position:absolute;font-family:"Open Sans",sans-serif;font-size:3.4px;line-height:4.4px;color:#9a9a9a;width:60px}

  /* graph */
  .bar-label{position:absolute;width:30px;text-align:center;font-family:"Open Sans",sans-serif;font-weight:600;font-size:3.2px;color:var(--orange-deep)}
  .bar-note{position:absolute;width:22px;text-align:center;font-family:"Open Sans",sans-serif;font-size:2px;line-height:2.6px;color:#888}
  .axis-label{position:absolute;left:37px;font-family:"Open Sans",sans-serif;font-size:3px;color:#999}

  /* services */
  .service-icon{position:absolute;top:69px;width:47px;height:40px;border:1.2px solid var(--orange);display:flex;align-items:center;justify-content:center}
  .service-text{position:absolute;top:119px;width:84px;font-weight:300;font-size:6.6px;line-height:12px;color:var(--ink-soft);text-align:justify}

  /* what */
  .what-photo{position:absolute;left:23px;top:110px;width:435px;height:134px;background:linear-gradient(90deg,#f4f4f4 0%,#e6e6e6 35%,#f7f7f7 55%,#dcdcdc 80%,#efefef 100%)}

  /* divider + thanks */
  .confetti{position:absolute;background:radial-gradient(ellipse at center,rgba(232,80,30,.10) 0%,rgba(120,170,60,.07) 45%,rgba(255,255,255,0) 72%)}
  .mega-brand{position:absolute;left:0;right:0;text-align:center;font-weight:700;line-height:1;color:var(--ink);letter-spacing:1px}
  .ruled-title{position:absolute;text-align:center;font-weight:600;color:var(--ink);border-top:1.5px solid var(--orange);border-bottom:1.5px solid var(--orange);line-height:1}
  .ruled-title .accent{color:var(--orange)}
  .road-photo{position:absolute;background:linear-gradient(160deg,rgba(255,255,255,0) 10%,#c9c9c9 45%,#8a8a8a 80%,#b5b5b5 100%)}
  .phone-line{position:absolute;left:181px;top:225px;display:flex;align-items:center;gap:7px;font-weight:400;font-size:13px;color:var(--ink)}
</style>
</head>
<body>

<!-- Slide 01: title -->
<section class="slide col-left row-1">
  <div class="title-brand">HAULWAY</div>
  <div class="band" style="top:82px"></div>
  <div class="hero-photo" role="img" aria-label="Black and white photo of a semi truck on an open road under a cloudy sky"></div>
  <div class="hero-title">United for Independence</div>
  <div class="band" style="top:228px"></div>
  <div class="page-no">PAGE <b>01</b></div>
</section>

<!-- Slide 05: why choose us -->
<section class="slide col-right row-1">
  <div class="brand-mini">HAULWAY</div>
  <h2 class="heading" style="left:39px;top:18px">WHY CHOOSE <span class="accent">US</span></h2>
  <p class="body-copy" style="left:39px;top:53px;width:178px">Sed ut perspiciatis unde omnis iste natus error sit voluptatem accusantium doloremque laudantium, totam rem aperiam, eaque ipsa quae ab illo inventore veritatis et quasi architecto beatae vitae dicta sunt explicabo. Nemo enim ipsam voluptatem quia voluptas sit aspernatur aut odit aut fugit, sed quia consequuntur magni dolores eos qui ratione voluptatem sequi nesciunt. Neque porro quisquam est, qui dolorem ipsum quia dolor sit amet, consectetur, adipisci velit, sed quia non numquam eius modi tempora incidunt ut labore et dolore magnam aliquam quaerat voluptatem.Sed ut perspiciatis unde omnis iste natus error sit voluptatem accusantium doloremque laudantium, totam rem aperiam, eaque ipsa quae ab illo inventore veritatis et quasi architecto beatae vitae dicta sunt explicabo. Nemo enim ipsam voluptatem quia voluptas sit aspernatur aut odit aut fugit, sed quia consequuntu</p>
  <svg class="abs" style="left:0;top:0" width="458" height="257" viewBox="0 0 458 257" aria-hidden="true">
    <defs>
      <linearGradient id="ring-gold" x1="0" y1="0" x2="1" y2="1"><stop offset="0" stop-color="#ffd36b"/><stop offset="1" stop-color="#f28a4a"/></linearGradient>
      <linearGradient id="ring-pink" x1="0" y1="0" x2="1" y2="1"><stop offset="0" stop-color="#f0557a"/><stop offset="1" stop-color="#d8305a"/></linearGradient>
      <linearGradient id="ring-violet" x1="0" y1="0" x2="1" y2="1"><stop offset="0" stop-color="#c0539a"/><stop offset="1" stop-color="#8a3b8f"/></linearGradient>
      <linearGradient id="ring-blue" x1="0" y1="0" x2="1" y2="1"><stop offset="0" stop-color="#3fb7e0"/><stop offset="1" stop-color="#2a7fc6"/></linearGradient>
    </defs>
    <line x1="244" y1="26" x2="244" y2="229" stroke="#e2e2e2" stroke-width="1"/>
    <g stroke="#d0d0d0" stroke-width=".6" stroke-dasharray="2 2">
      <line x1="244" y1="72" x2="268" y2="72"/>
      <line x1="244" y1="113" x2="331" y2="113"/>
      <line x1="244" y1="152" x2="268" y2="152"/>
      <line x1="244" y1="195" x2="331" y2="195"/>
    </g>
    <g>
      <circle cx="290" cy="72" r="20" fill="#fff" stroke="#eeeeee" stroke-width="1"/>
      <circle cx="290" cy="72" r="16" fill="none" stroke="url(#ring-gold)" stroke-width="4"/>
      <circle cx="290" cy="72" r="2.5" fill="#f28a4a"/>
      <circle cx="353" cy="113" r="20" fill="#fff" stroke="#eeeeee" stroke-width="1"/>
      <circle cx="353" cy="113" r="16" fill="none" stroke="url(#ring-pink)" stroke-width="4"/>
      <circle cx="353" cy="113" r="2.5" fill="#d8305a"/>
      <circle cx="290" cy="152" r="20" fill="#fff" stroke="#eeeeee" stroke-width="1"/>
      <circle cx="290" cy="152" r="16" fill="none" stroke="url(#ring-violet)" stroke-width="4"/>
      <circle cx="290" cy="152" r="2.5" fill="#8a3b8f"/>
      <circle cx="353" cy="195" r="20" fill="#fff" stroke="#eeeeee" stroke-width="1"/>
      <circle cx="353" cy="195" r="16" fill="none" stroke="url(#ring-blue)" stroke-width="4"/>
      <circle cx="353" cy="195" r="2.5" fill="#2a7fc6"/>
    </g>
    <g fill="none" stroke-width="1">
      <polyline points="314,68 317,72 314,76" stroke="#f28a4a"/>
      <polyline points="377,109 380,113 377,117" stroke="#d8305a"/>
      <polyline points="314,148 317,152 314,156" stroke="#8a3b8f"/>
      <polyline points="377,191 380,195 377,199" stroke="#2a7fc6"/>
    </g>
  </svg>
  <div class="option-title" style="left:326px;top:59px">Option header</div>
  <div class="option-text" style="left:326px;top:68px">Lorem ipsum dolor sit amet, consectetur adipiscing elit, sed do eiusmod tempor incididunt ut labore et dolore magna aliqua.</div>
  <div class="option-title" style="left:389px;top:100px">Option header</div>
  <div class="option-text" style="left:389px;top:109px">Lorem ipsum dolor sit amet, consectetur adipiscing elit, sed do eiusmod tempor incididunt ut labore et dolore magna aliqua.</div>
  <div class="option-title" style="left:326px;top:139px">Option header</div>
  <div class="option-text" style="left:326px;top:148px">Lorem ipsum dolor sit amet, consectetur adipiscing elit, sed do eiusmod tempor incididunt ut labore et dolore magna aliqua.</div>
  <div class="option-title" style="left:393px;top:183px">Option header</div>
  <div class="option-text" style="left:393px;top:192px">Lorem ipsum dolor sit amet, consectetur adipiscing elit, sed do eiusmod tempor incididunt ut labore et dolore magna aliqua.</div>
  <div class="page-no">PAGE <b>05</b></div>
</section>

<!-- Slide 02: about us -->
<section class="slide col-left row-2">
  <div class="brand-mini">HAULWAY</div>
  <h2 class="heading" style="left:40px;top:19px">ABOUT <span class="accent">US</span></h2>
  <p class="body-copy" style="left:39px;top:53px;width:179px">Sed ut perspiciatis unde omnis iste natus error sit voluptatem accusantium doloremque laudantium, totam rem aperiam, eaque ipsa quae ab illo inventore veritatis et quasi architecto beatae vitae dicta sunt explicabo. Nemo enim ipsam voluptatem quia voluptas sit aspernatur aut odit aut fugit, sed quia consequuntur magni dolores eos qui ratione voluptatem sequi nesciunt. Neque porro quisquam est, qui dolorem ipsum quia dolor sit amet, consectetur, adipisci velit, sed quia non numquam eius modi tempora incidunt ut labore et dolore magnam aliquam quaerat voluptatem.Sed ut perspiciatis unde omnis iste natus error sit voluptatem accusantium doloremque laudantium, totam rem aperiam, eaque ipsa quae ab illo inventore veritatis et quasi architecto beatae vitae dicta sunt explicabo. Nemo enim ipsam voluptatem quia voluptas sit aspernatur aut odit aut fugit, sed quia consequuntu</p>
  <p class="body-copy" style="left:235px;top:53px;width:179px">Sed ut perspiciatis unde omnis iste natus error sit voluptatem accusantium doloremque laudantium, totam rem aperiam, eaque ipsa quae ab illo inventore veritatis et quasi architecto beatae vitae dicta sunt explicabo. Nemo enim ipsam voluptatem quia voluptas sit aspernatur aut odit aut fugit, sed quia consequuntur magni dolores eos qui ratione voluptatem sequi nesciunt. Neque porro quisquam est, qui dolorem ipsum quia dolor sit amet, consectetur, adipisci velit, sed quia non numquam eius modi tempora incidunt ut labore et dolore magnam aliquam quaerat voluptatem.Sed ut perspiciatis unde omnis iste natus error sit voluptatem accusantium doloremque laudantium, totam rem aperiam, eaque ipsa quae ab illo inventore veritatis et quasi architecto beatae vitae dicta sunt explicabo. Nemo enim ipsam voluptatem quia voluptas sit aspernatur aut odit aut fugit, sed quia consequuntu</p>
  <div class="page-no">PAGE <b>02</b></div>
</section>

<!-- Slide 06: our graph -->
<section class="slide col-right row-2">
  <div class="brand-mini">HAULWAY</div>
  <h2 class="heading" style="left:44px;top:19px">OUR <span class="accent">GRAPH</span></h2>
  <p class="body-copy" style="left:45px;top:56px;width:358px;line-height:12px">Sed ut perspiciatis unde omnis iste natus error sit voluptatem accusantium doloremque ium, totam rem aperiam, eaque ipsa quae ab illo inventore veritatis et quasi architecto beatae vitae icta sunt explicabemo enim psam voluptatem quia voluptas sit aspernatur aut odit aut fugit, sed quia consequuntur magni dolores eos qui ratione voluptatem ectetur, adipisci velit, sed quia non numquam eius modi tempora incidunt</p>
  <div class="axis-label" style="top:99px">100%</div>
  <div class="axis-label" style="top:110px">90%</div>
  <div class="axis-label" style="top:121px">80%</div>
  <div class="axis-label" style="top:132px">70%</div>
  <div class="axis-label" style="top:143px">60%</div>
  <div class="axis-label" style="top:154px">50%</div>
  <div class="axis-label" style="top:165px">40%</div>
  <div class="axis-label" style="top:176px">30%</div>
  <div class="axis-label" style="top:187px">20%</div>
  <div class="axis-label" style="top:198px">10%</div>
  <div class="axis-label" style="top:209px">0%</div>
  <svg class="abs" style="left:0;top:0" width="458" height="257" viewBox="0 0 458 257" aria-label="Bar chart rising from 10% to 100% across ten categories">
    <g stroke="var(--grid)" stroke-width=".5">
      <line x1="50" y1="101" x2="410" y2="101"/><line x1="50" y1="112" x2="410" y2="112"/>
      <line x1="50" y1="123" x2="410" y2="123"/><line x1="50" y1="134" x2="410" y2="134"/>
      <line x1="50" y1="145" x2="410" y2="145"/><line x1="50" y1="156" x2="410" y2="156"/>
      <line x1="50" y1="167" x2="410" y2="167"/><line x1="50" y1="178" x2="410" y2="178"/>
      <line x1="50" y1="189" x2="410" y2="189"/><line x1="50" y1="200" x2="410" y2="200"/>
      <line x1="50" y1="211" x2="410" y2="211"/>
    </g>
    <g>
      <rect x="65" y="200" width="20" height="12" fill="#9a2a10"/><ellipse cx="75" cy="212" rx="10" ry="2.5" fill="#9a2a10"/><ellipse cx="75" cy="200" rx="10" ry="2.5" fill="#b84228"/>
      <rect x="100" y="188" width="20" height="24" fill="#b5361a"/><ellipse cx="110" cy="212" rx="10" ry="2.5" fill="#b5361a"/><ellipse cx="110" cy="188" rx="10" ry="2.5" fill="#cc5236"/>
      <rect x="136" y="178" width="20" height="34" fill="#c63a1e"/><ellipse cx="146" cy="212" rx="10" ry="2.5" fill="#c63a1e"/><ellipse cx="146" cy="178" rx="10" ry="2.5" fill="#da563a"/>
      <rect x="171" y="167" width="20" height="45" fill="#d5401f"/><ellipse cx="181" cy="212" rx="10" ry="2.5" fill="#d5401f"/><ellipse cx="181" cy="167" rx="10" ry="2.5" fill="#e55c3e"/>
      <rect x="207" y="155" width="20" height="57" fill="#dc4428"/><ellipse cx="217" cy="212" rx="10" ry="2.5" fill="#dc4428"/><ellipse cx="217" cy="155" rx="10" ry="2.5" fill="#ea6248"/>
      <rect x="242" y="144" width="20" height="68" fill="#e0503a"/><ellipse cx="252" cy="212" rx="10" ry="2.5" fill="#e0503a"/><ellipse cx="252" cy="144" rx="10" ry="2.5" fill="#ec6c56"/>
      <rect x="278" y="134" width="20" height="78" fill="#e65c48"/><ellipse cx="288" cy="212" rx="10" ry="2.5" fill="#e65c48"/><ellipse cx="288" cy="134" rx="10" ry="2.5" fill="#f07a66"/>
      <rect x="313" y="122" width="20" height="90" fill="#eb6a57"/><ellipse cx="323" cy="212" rx="10" ry="2.5" fill="#eb6a57"/><ellipse cx="323" cy="122" rx="10" ry="2.5" fill="#f38774"/>
      <rect x="348" y="111" width="20" height="101" fill="#ef7865"/><ellipse cx="358" cy="212" rx="10" ry="2.5" fill="#ef7865"/><ellipse cx="358" cy="111" rx="10" ry="2.5" fill="#f69583"/>
      <rect x="384" y="101" width="20" height="111" fill="#f38a78"/><ellipse cx="394" cy="212" rx="10" ry="2.5" fill="#f38a78"/><ellipse cx="394" cy="101" rx="10" ry="2.5" fill="#f8a596"/>
    </g>
    <g fill="#d33a1c">
      <circle cx="75" cy="221" r="1.5"/><circle cx="110" cy="221" r="1.5"/><circle cx="146" cy="221" r="1.5"/><circle cx="181" cy="221" r="1.5"/><circle cx="217" cy="221" r="1.5"/>
      <circle cx="252" cy="221" r="1.5"/><circle cx="288" cy="221" r="1.5"/><circle cx="323" cy="221" r="1.5"/><circle cx="358" cy="221" r="1.5"/><circle cx="394" cy="221" r="1.5"/>
    </g>
  </svg>
  <div class="bar-label" style="left:60px;top:225px">TITLE HERE</div><div class="bar-note" style="left:64px;top:230px">Lorem ipsum dolor sit amet adipiscing</div>
  <div class="bar-label" style="left:95px;top:225px">TITLE HERE</div><div class="bar-note" style="left:99px;top:230px">Lorem ipsum dolor sit amet adipiscing</div>
  <div class="bar-label" style="left:131px;top:225px">TITLE HERE</div><div class="bar-note" style="left:135px;top:230px">Lorem ipsum dolor sit amet adipiscing</div>
  <div class="bar-label" style="left:166px;top:225px">TITLE HERE</div><div class="bar-note" style="left:170px;top:230px">Lorem ipsum dolor sit amet adipiscing</div>
  <div class="bar-label" style="left:202px;top:225px">TITLE HERE</div><div class="bar-note" style="left:206px;top:230px">Lorem ipsum dolor sit amet adipiscing</div>
  <div class="bar-label" style="left:237px;top:225px">TITLE HERE</div><div class="bar-note" style="left:241px;top:230px">Lorem ipsum dolor sit amet adipiscing</div>
  <div class="bar-label" style="left:273px;top:225px">TITLE HERE</div><div class="bar-note" style="left:277px;top:230px">Lorem ipsum dolor sit amet adipiscing</div>
  <div class="bar-label" style="left:308px;top:225px">TITLE HERE</div><div class="bar-note" style="left:312px;top:230px">Lorem ipsum dolor sit amet adipiscing</div>
  <div class="bar-label" style="left:343px;top:225px">TITLE HERE</div><div class="bar-note" style="left:347px;top:230px">Lorem ipsum dolor sit amet adipiscing</div>
  <div class="bar-label" style="left:379px;top:225px">TITLE HERE</div><div class="bar-note" style="left:383px;top:230px">Lorem ipsum dolor sit amet adipiscing</div>
  <div class="page-no">PAGE <b>06</b></div>
</section>

<!-- Slide 03: our services -->
<section class="slide col-left row-3">
  <div class="brand-mini">HAULWAY</div>
  <h2 class="heading" style="left:40px;top:18px">OUR <span class="accent">SERVICES</span></h2>
  <div class="service-icon" style="left:34px">
    <svg width="22" height="16" viewBox="0 0 22 16" aria-label="Delivery truck icon"><path d="M1 1h12v10H1z M13 4h4l4 4v3h-8z" fill="var(--ink)"/><circle cx="5" cy="12.5" r="2.4" fill="var(--ink)" stroke="#fff" stroke-width="1"/><circle cx="17" cy="12.5" r="2.4" fill="var(--ink)" stroke="#fff" stroke-width="1"/></svg>
  </div>
  <div class="service-icon" style="left:136px">
    <svg width="14" height="17" viewBox="0 0 14 17" aria-label="Document icon"><path d="M0 0h9l5 5v12H0z" fill="var(--ink)"/><path d="M9 0v5h5" fill="#fff"/></svg>
  </div>
  <div class="service-icon" style="left:239px">
    <svg width="17" height="17" viewBox="0 0 17 17" aria-label="Pencil icon"><path d="M0 13.5V17h3.5L13.5 7 10 3.5z M11.5 2 13 .5a1.5 1.5 0 0 1 2 0L16.5 2a1.5 1.5 0 0 1 0 2L15 5.5z" fill="var(--ink)"/></svg>
  </div>
  <div class="service-icon" style="left:342px">
    <svg width="18" height="17" viewBox="0 0 24 23" aria-label="Star icon"><path d="M12 0l3.5 7.4 8.1 1-6 5.6 1.6 8L12 18l-7.2 4 1.6-8-6-5.6 8.1-1z" fill="var(--ink)"/></svg>
  </div>
  <p class="service-text" style="left:34px">Sed ut perspiciatis unde omnis iste natus error sit voluptatem accusantium doloremque ium, totam rem aperiam, eaque ipsa quae ab illo inventore veritatis et quasi architecto beatae vitae icta sunt explicabemo enim psam voluptatem quia voluptas</p>
  <p class="service-text" style="left:136px">Sed ut perspiciatis unde omnis iste natus error sit voluptatem accusantium doloremque ium, totam rem aperiam, eaque ipsa quae ab illo inventore veritatis et quasi architecto beatae vitae icta sunt explicabemo enim psam voluptatem quia voluptas</p>
  <p class="service-text" style="left:239px">Sed ut perspiciatis unde omnis iste natus error sit voluptatem accusantium doloremque ium, totam rem aperiam, eaque ipsa quae ab illo inventore veritatis et quasi architecto beatae vitae icta sunt explicabemo enim psam voluptatem quia voluptas</p>
  <p class="service-text" style="left:342px">Sed ut perspiciatis unde omnis iste natus error sit voluptatem accusantium doloremque ium, totam rem aperiam, eaque ipsa quae ab illo inventore veritatis et quasi architecto beatae vitae icta sunt explicabemo enim psam voluptatem quia voluptas</p>
  <div class="page-no">PAGE <b>03</b></div>
</section>

<!-- Slide 07: what -->
<section class="slide col-right row-3">
  <div class="brand-mini">HAULWAY</div>
  <h2 class="heading" style="left:41px;top:18px;width:101px;text-align:center;border-bottom-color:var(--orange)">WHAT?</h2>
  <p class="body-copy" style="left:45px;top:56px;width:370px;font-size:9.4px;line-height:12px;text-align:left;color:var(--ink)">Haulway reinvents the shipper and carrier relationship through a specialized process and custom technology designed specifically to address the areas the freight industry ignores.</p>
  <div class="what-photo" role="img" aria-label="Photo of a white box truck and a white semi truck cab side by side"></div>
  <div class="abs" style="left:264px;top:104px;width:194px;height:6px;background:var(--orange)"></div>
  <div class="abs" style="left:27px;top:215px;width:249px;height:6px;background:linear-gradient(90deg,var(--orange) 70%,rgba(232,80,30,0))"></div>
  <div class="page-no">PAGE <b>07</b></div>
</section>

<!-- Slide 04: section divider -->
<section class="slide col-left row-4">
  <div class="brand-mini">HAULWAY</div>
  <div class="confetti" role="img" aria-label="Colourful confetti and firework burst" style="left:60px;top:30px;width:340px;height:150px"></div>
  <div class="mega-brand" style="top:92px;font-size:66px">HAULWAY</div>
  <div class="ruled-title" style="left:149px;top:198px;width:173px;font-size:20px;padding:1px 0">SECTION DIVIDER <span class="accent">TITLE</span></div>
  <div class="page-no">PAGE <b>04</b></div>
</section>

<!-- Slide 08: thank you -->
<section class="slide col-right row-4">
  <div class="road-photo" role="img" aria-label="Black and white photo of a semi truck on a highway" style="left:300px;top:120px;width:158px;height:137px"></div>
  <div class="confetti" role="img" aria-label="Colourful confetti and firework burst" style="left:60px;top:0;width:340px;height:150px"></div>
  <div class="mega-brand" style="top:56px;font-size:68px">HAULWAY</div>
  <div class="ruled-title" style="left:116px;top:155px;width:226px;font-size:42px;padding:3px 0">THANK <span class="accent">YOU</span></div>
  <div class="phone-line">
    <svg width="20" height="20" viewBox="0 0 20 20" aria-label="Phone icon"><circle cx="10" cy="10" r="10" fill="var(--orange)"/><path d="M7.2 5.2l1.6 2.4-1 1.2a6 6 0 0 0 3.4 3.4l1.2-1 2.4 1.6-.8 1.8c-4.2.2-8.6-4.2-8.4-8.4z" fill="#fff"/></svg>
    <span>555-014-2273</span>
  </div>
  <div class="page-no">PAGE <b>08</b></div>
</section>

</body>
</html>
```